Bramblewood Joinery Website

My client Bramblewood Joinery is looking for a redesign for a Word Press Website. Their current site is at www.bramblewoodjoinery.example They are a custom cabinet company, but also create bathroom, living room, bar and entertainment and bedroom cabinets too. They would like a design that emulates the master craftsman work they do yet a contemporary style.

Their current site was designed using Flash elements.

Target Market(s)

Home owners and builders of high end homes

Industry/Entity Type

Entertainment

Font styles to use
Serif
Decorative

Requirements
Must have
• Must show their work and logo using a contemporary style.
Nice to have
• Sliders that showcase their projects.

```html
<!DOCTYPE html>
<html lang="en">
<head>
<meta charset="utf-8">
<title>Bramblewood Joinery</title>
<link rel="stylesheet" href="https://fonts.googleapis.com/css2?family=Varela+Round&family=Nunito+Sans:ital,wght@0,400;0,600;1,400&display=swap">
<style>
:root{
  --green:#2faa2f;
  --green-text:#37a82f;
  --dark:#2b2b2b;
  --footer:#2a2a2a;
  --text:#444;
  --muted:#888;
  --line:#e2e2e2;
  --frame:#dcdcdc;
  --white:#fff;
}
*{box-sizing:border-box;margin:0;padding:0}
html,body{width:798px;height:1200px;overflow:hidden;background:var(--white)}
body{position:relative;font-family:"Nunito Sans",sans-serif;color:var(--text);font-size:9px;line-height:14px}
.abs{position:absolute}
h1,h2,h3{font-family:"Varela Round",sans-serif;font-weight:400;color:var(--green-text)}
h2{font-size:16px;line-height:20px}
h3{font-size:11px;line-height:14px}
.btn{position:absolute;background:var(--dark);color:var(--white);font-size:10px;display:flex;align-items:center;justify-content:center;border-radius:2px}

.contact{top:13px;right:48px;font-size:12px;display:flex;align-items:center;gap:5px;color:#222;font-family:"Varela Round",sans-serif}
.contact span{color:var(--green-text)}
.nav{left:50px;top:42px;width:699px;height:29px;background:var(--dark);display:flex;align-items:center;color:#eee;font-size:9px}
.nav .left,.nav .right{display:flex;position:absolute}
.nav .left{left:13px;gap:25px}
.nav .right{left:419px;gap:25px}
.brand{left:354px;top:10px;width:92px;height:92px;border-radius:50%;background:var(--white);border:4px solid var(--dark);box-shadow:0 0 0 4px var(--white);display:flex;align-items:center;justify-content:center;text-align:center;font-family:"Varela Round",sans-serif;font-size:11px;line-height:13px;color:var(--green-text)}

.hero{left:50px;top:73px;width:699px;height:273px;overflow:hidden}
.hero-photo{position:absolute;inset:0;background:
  radial-gradient(ellipse 120px 60px at 560px 70px,rgba(240,232,218,.85),transparent 70%),
  radial-gradient(ellipse 160px 70px at 520px 200px,rgba(235,230,222,.8),transparent 70%),
  linear-gradient(180deg,#4a3a2e 0%,#8c7a66 35%,#cfc6b8 60%,#5b4a3a 100%)}
.hero svg{position:absolute;left:0;top:0}
.hero h1{position:absolute;left:24px;top:50px;color:var(--white);font-size:25px;line-height:30px;width:280px}
.hero .btn{left:24px;top:181px;width:97px;height:29px;font-size:12px;border-radius:0}
.dots{position:absolute;left:25px;top:249px;display:flex;gap:5px}
.dots i{width:8px;height:8px;border-radius:50%;background:var(--dark)}
.dots i:first-child{background:var(--white)}

.rule{position:absolute;height:1px;background:var(--line)}
.photo{position:absolute;border:2px solid var(--frame)}
.photo div{width:100%;height:100%}
.card h3{margin-bottom:2px}

.quote{font-style:italic;font-size:9px;line-height:14px;color:var(--text)}
.quote b{color:#bbb;font-size:14px;font-style:normal;margin-right:4px}
.author{font-style:italic;color:var(--green-text);font-size:9px}

.newsletter{left:469px;top:824px;width:280px;height:114px;border:2px solid var(--frame);background:#f2f2f2;padding:14px 15px}
.newsletter p{font-style:italic;margin-top:6px}
.field{margin-top:8px;height:30px;border:1px solid #ccc;background:var(--white);display:flex;align-items:center;justify-content:space-between;padding:0 3px 0 10px;font-style:italic;color:var(--muted);font-size:8px}
.field i{width:29px;height:22px;background:var(--green);display:flex;align-items:center;justify-content:center}

.footer{left:0;top:1127px;width:798px;height:73px;background:var(--footer);color:var(--muted);font-size:8px}
.footer .copy{position:absolute;left:50px;top:22px}
.footer .copy em{font-style:normal;color:#ccc}
.footer .links{position:absolute;left:50px;top:39px}
.social{position:absolute;left:669px;top:19px;display:flex;gap:11px}
.social i{width:19px;height:19px;background:#4a4a4a;border:1px solid #666;border-radius:3px}
</style>
</head>
<body>

<div class="abs contact">
  <svg width="16" height="16" viewBox="0 0 16 16"><circle cx="8" cy="8" r="8" fill="#d33"/><path d="M5 4.5l1.6-.5 1 2-1 .8a5 5 0 0 0 2.6 2.6l.8-1 2 1-.5 1.6C9 11.5 4.5 7 5 4.5z" fill="#fff"/></svg>
  <span>Contact Us:</span> 555.014.2300
</div>

<nav class="abs nav">
  <div class="left"><span>Home</span><span>Who We Are</span><span>Getting Statred</span><span>Professional</span></div>
  <div class="right"><span>Customer Experience</span><span>Portfolio</span><span>Cabinet Hardaware</span></div>
</nav>

<section class="abs hero">
  <div class="hero-photo" role="img" aria-label="Photo of a finished custom kitchen with white cabinets and pendant lights"></div>
  <svg width="699" height="273" viewBox="0 0 699 273"><path d="M0 0H328Q300 120 310 273H0Z" fill="var(--green)"/></svg>
  <h1>Kansas City's Premier Custom Kitchen Cabinet Design Company</h1>
  <div class="btn">READ MORE</div>
  <div class="dots"><i></i><i></i><i></i><i></i></div>
</section>
<div class="abs brand">Bramblewood<br>Joinery</div>

<h2 class="abs" style="left:50px;top:370px">Welcome to Our Website</h2>
<p class="abs" style="left:50px;top:396px;width:384px">At Bramblewood Joinery, we've been designing and manufacturing the Midwest's finest custom cabinets and fixtures since 1966. From single cabinets to room remodels to entire home installations, our expert artisans help turn the house you live in to the home you've always dreamed of.</p>
<div class="btn" style="left:50px;top:465px;width:82px;height:25px">Read More</div>
<div class="rule" style="left:50px;top:508px;width:381px"></div>

<h2 class="abs" style="left:50px;top:523px">What We Do</h2>
<div class="photo" style="left:50px;top:551px;width:183px;height:117px"><div role="img" aria-label="Bathroom with curved blue counter and tiled cabinets" style="background:radial-gradient(ellipse 90px 30px at 90px 85px,#5ed0ea,transparent 75%),linear-gradient(180deg,#1b2e2c 0%,#2f5e5a 45%,#3aa0bd 70%,#5a4430 100%)"></div></div>
<div class="photo" style="left:247px;top:551px;width:183px;height:117px"><div role="img" aria-label="Living room with wood cabinetry and vaulted ceiling" style="background:radial-gradient(ellipse 60px 40px at 130px 40px,rgba(240,200,150,.6),transparent 75%),linear-gradient(180deg,#6a3a20 0%,#9a5a2f 45%,#5a2f1a 80%,#3a1a10 100%)"></div></div>
<div class="abs card" style="left:50px;top:680px;width:185px"><h3>Bath Room</h3><p>Aliquam molestie, mi et imperdiet euismod, dui purus auctor tellus, et interdum lacus lectus et ante.</p></div>
<div class="abs card" style="left:247px;top:680px;width:185px"><h3>Living Room</h3><p>Aliquam molestie, mi et imperdiet euismod, dui purus auctor tellus, et interdum lacus lectus et ante.</p></div>
<div class="photo" style="left:50px;top:755px;width:183px;height:117px"><div role="img" aria-label="Home bar with dark wood shelving and stools" style="background:radial-gradient(ellipse 70px 35px at 110px 40px,rgba(230,170,110,.45),transparent 75%),linear-gradient(180deg,#3a140c 0%,#7a2a1a 50%,#4a1a10 75%,#1e0a06 100%)"></div></div>
<div class="photo" style="left:247px;top:755px;width:183px;height:117px"><div role="img" aria-label="Bedroom with white furniture set" style="background:radial-gradient(ellipse 60px 25px at 110px 75px,#b8692c,transparent 75%),linear-gradient(180deg,#8a8478 0%,#e2ddd2 45%,#cfc8b8 70%,#8a6a3c 100%)"></div></div>
<div class="abs card" style="left:50px;top:884px;width:185px"><h3>Bar and Entertainment</h3><p>Aliquam molestie, mi et imperdiet euismod, dui purus auctor tellus, et interdum lacus lectus et ante.</p></div>
<div class="abs card" style="left:247px;top:884px;width:185px"><h3>BedRoom</h3><p>Aliquam molestie, mi et imperdiet euismod, dui purus auctor tellus, et interdum lacus lectus et ante.</p></div>

<h2 class="abs" style="left:468px;top:371px">Watch Our Video</h2>
<div class="abs" style="left:468px;top:400px;width:281px;height:150px;border:2px solid var(--frame);background:radial-gradient(circle at 50% 45%,#1a1a1a,#000 60%);display:flex;flex-direction:column;align-items:center;justify-content:center;gap:10px">
  <svg width="44" height="44" viewBox="0 0 44 44"><circle cx="22" cy="22" r="19" fill="none" stroke="#fff" stroke-width="3"/><path d="M17 12l14 10-14 10z" fill="#fff"/></svg>
  <span style="color:#ccc;font-size:9px;letter-spacing:2px">BRAMBLEWOOD JOINERY</span>
</div>
<div class="rule" style="left:468px;top:567px;width:281px"></div>

<h2 class="abs" style="left:468px;top:580px">Customer Experience</h2>
<p class="abs quote" style="left:468px;top:613px;width:265px"><b>&ldquo;</b>When one of the top homebuilders in Kansas City chooses your cabinets for his personal home, then you know you make a pretty good product.</p>
<p class="abs author" style="left:468px;top:666px">Builder, Dale Hartwell</p>
<div class="rule" style="left:468px;top:690px;width:281px"></div>
<p class="abs quote" style="left:468px;top:701px;width:265px"><b>&ldquo;</b>When one of the top homebuilders in Kansas City chooses your cabinets for his personal home, then you know you make a pretty good product.</p>
<p class="abs author" style="left:468px;top:754px">Builder, Dale Hartwell</p>
<div class="btn" style="left:649px;top:781px;width:100px;height:25px">More Expereince</div>

<div class="abs newsletter">
  <h2>Newsletter Sign Up</h2>
  <p>Aliquam molestie, mi et imperdiet euismod, dui purus auctor tellus, et interdum lacus lectus et ante.</p>
  <div class="field">Enter Email Address <i><svg width="12" height="12" viewBox="0 0 12 12"><path d="M3 1l5 5-5 5" fill="none" stroke="#fff" stroke-width="2.5"/></svg></i></div>
</div>

<div class="rule" style="left:50px;top:969px;width:699px"></div>
<h2 class="abs" style="left:50px;top:984px">Photo Gallery</h2>
<div class="photo" style="left:50px;top:1013px;width:160px;height:92px"><div role="img" aria-label="Kitchen with white cabinets and built-in oven" style="background:radial-gradient(ellipse 40px 30px at 35px 35px,#222,transparent 80%),linear-gradient(180deg,#cfc9be 0%,#e6e1d8 55%,#5a3a26 80%,#3a2416 100%)"></div></div>
<div class="photo" style="left:229px;top:1013px;width:160px;height:92px"><div role="img" aria-label="Black kitchen island" style="background:radial-gradient(ellipse 60px 35px at 80px 55px,#111,transparent 85%),linear-gradient(180deg,#7a6a58 0%,#3a3028 45%,#2a1a10 100%)"></div></div>
<div class="photo" style="left:408px;top:1013px;width:160px;height:92px"><div role="img" aria-label="Dark island with panelled sides" style="background:radial-gradient(ellipse 55px 35px at 80px 60px,#151515,transparent 85%),linear-gradient(180deg,#e0ddd5 0%,#b8b2a6 35%,#4a3a2c 100%)"></div></div>
<div class="photo" style="left:587px;top:1013px;width:160px;height:92px"><div role="img" aria-label="Bright bathroom with white vanity" style="background:radial-gradient(ellipse 40px 30px at 125px 30px,#fff,transparent 80%),linear-gradient(180deg,#d8d2c4 0%,#f0ede6 50%,#bdb5a5 100%)"></div></div>

<footer class="abs footer">
  <p class="copy">Copyright © 2015 <em>Bramblewood Joinery</em>. All Right Reserved</p>
  <p class="links">Privacy Policy &nbsp;|&nbsp; Term of Services</p>
  <div class="social"><i></i><i></i><i></i></div>
</footer>

</body>
</html>
```